Salon and Spa Distributor Business Card

Need a business card. We are are distributor in the salon and spa industry. We identify with natural beauty. Need a card with:
Company Name: Petal Quarry"
Title: "President & CEO"
Address
Company Phone number
email
website
Tag Line:" The Professional Salon Source"

Industry/Entity Type

Business

Contact Information for Business Card

Name: Dov Strommen
Title: "President & CEO"
Address: 31 Harlow Ln, Bexmoor, NJ 07813
Company Phone number: 800-463-5918
email: dovstrommen@petalquarry.example
website: www.petalquarry.example

Requirements
Should not have
• No black backgrounds

```html
<!DOCTYPE html>
<html lang="en">
<head>
<meta charset="utf-8">
<title>Petal Quarry — Business Card</title>
<link href="https://fonts.googleapis.com/css2?family=Questrial&display=swap" rel="stylesheet">
<style>
  :root {
    --page-bg: #e8eae6;
    --card-white: #f5f5f5;
    --brand-green: #2f8a2c;
    --deep-green: #2a7a3a;
    --fresh-green: #62ad36;
    --text-grey: #555a55;
    --rule-grey: #dcdcdc;
  }
  * { margin: 0; padding: 0; box-sizing: border-box; }
  html, body {
    width: 1200px;
    height: 972px;
    overflow: hidden;
    background: var(--page-bg);
    font-family: "Questrial", "Century Gothic", sans-serif;
  }
  .canvas {
    position: relative;
    width: 1200px;
    height: 972px;
  }
  .card {
    position: absolute;
    left: 323px;
    width: 554px;
    height: 316px;
    border-radius: 16px;
    overflow: hidden;
    box-shadow: 0 4px 14px rgba(0, 0, 0, 0.12);
  }
  .card--front {
    top: 142px;
    background: var(--card-white);
  }
  .card--back {
    top: 513px;
    background: linear-gradient(115deg, var(--deep-green) 0%, #3f9436 45%, var(--fresh-green) 100%);
  }

  /* Front: brand block */
  .brand {
    position: absolute;
    left: 20px;
    width: 258px;
    top: 0;
    height: 316px;
    display: flex;
    flex-direction: column;
    align-items: center;
    justify-content: center;
    gap: 6px;
  }
  .brand__dot {
    width: 46px;
    height: 46px;
    border-radius: 50%;
    background: var(--brand-green);
    margin-bottom: 18px;
  }
  .brand__name {
    font-size: 34px;
    color: var(--brand-green);
    letter-spacing: 0.2px;
    line-height: 1;
  }
  .brand__tagline {
    font-size: 13.5px;
    color: var(--text-grey);
    letter-spacing: 0.3px;
  }

  .divider {
    position: absolute;
    left: 280px;
    top: 68px;
    width: 1px;
    height: 184px;
    background: var(--rule-grey);
  }

  /* Front: contact block */
  .contact {
    position: absolute;
    left: 307px;
    top: 80px;
    color: var(--text-grey);
  }
  .contact__name {
    font-size: 19px;
    color: var(--brand-green);
    text-transform: uppercase;
    letter-spacing: 0.3px;
    line-height: 22px;
  }
  .contact__title {
    font-size: 13.5px;
    line-height: 17px;
  }
  .contact__lines {
    list-style: none;
    margin-top: 24px;
    font-size: 12.8px;
    line-height: 16.5px;
  }
  .contact__label {
    color: var(--brand-green);
    font-weight: bold;
  }
  .contact__address {
    font-style: normal;
    margin-top: 15px;
    font-size: 13px;
    line-height: 16.5px;
  }

  /* Back */
  .back-brand {
    position: absolute;
    left: 270px;
    width: 240px;
    top: 124px;
    text-align: center;
    color: #ffffff;
  }
  .back-brand__name {
    font-size: 37px;
    line-height: 44px;
  }
  .back-brand__tagline {
    font-size: 14.5px;
    margin-top: 4px;
    letter-spacing: 0.3px;
  }
</style>
</head>
<body>
<main class="canvas">
  <section class="card card--front" aria-label="Business card front">
    <div class="brand">
      <span class="brand__dot" aria-hidden="true"></span>
      <span class="brand__name">Petal Quarry</span>
      <span class="brand__tagline">The Professional Salon Source</span>
    </div>
    <div class="divider"></div>
    <div class="contact">
      <p class="contact__name">Dov Strommen</p>
      <p class="contact__title">President &amp; CEO</p>
      <ul class="contact__lines">
        <li><span class="contact__label">T:</span> 800-463-5918</li>
        <li><span class="contact__label">E:</span> dovstrommen@petalquarry.example</li>
        <li><span class="contact__label">W:</span> www.petalquarry.example</li>
      </ul>
      <address class="contact__address">
        31 Harlow Ln<br>
        Bexmoor, NJ 07813
      </address>
    </div>
  </section>

  <section class="card card--back" aria-label="Business card back">
    <div class="back-brand">
      <p class="back-brand__name">Petal Quarry</p>
      <p class="back-brand__tagline">The Professional Salon Source</p>
    </div>
  </section>
</main>
</body>
</html>
```